Business Card Design Project

We are a construction company in Orange County, CA. We need a two sided business card. We would like the back to be our logo with web URL. Front should included Name, title, address, phone, fax and email address.

our address is
627 West Dorrance Blvd, Suite 308
Anaheim, CA 92718

Our logo files are attached.

Construction

```html
<!DOCTYPE html>
<html lang="en">
<head>
<meta charset="utf-8">
<title>Varden Business Card – Front and Back</title>
<link rel="stylesheet" href="https://fonts.googleapis.com/css2?family=PT+Sans:wght@400;700&display=swap">
<style>
  :root {
    --brand-blue: #1c4a7d;
    --ink-grey: #4a4a4a;
    --rule-grey: #c8c8c8;
    --card-white: #ffffff;
    --backdrop: #ececec;
  }
  * { box-sizing: border-box; margin: 0; padding: 0; }
  html, body {
    width: 1200px;
    height: 444px;
    overflow: hidden;
    background: var(--backdrop);
    font-family: "PT Sans", sans-serif;
  }
  .stage { position: relative; width: 1200px; height: 444px; }

  .card {
    position: absolute;
    top: 74px;
    width: 516px;
    height: 294px;
    background: var(--card-white);
    border-radius: 14px;
  }
  .card--front { left: 69px; }
  .card--back  { left: 615px; }

  .wordmark {
    position: absolute;
    color: var(--brand-blue);
    font-weight: 700;
    font-size: 54px;
    line-height: 1;
    letter-spacing: -1px;
  }
  .card--front .wordmark { left: 34px; top: 42px; }

  .divider {
    position: absolute;
    top: 130px;
    height: 2px;
    background: var(--rule-grey);
  }
  .divider--left  { left: 0; width: 302px; }
  .divider--right { right: 0; width: 30px; }

  .identity {
    position: absolute;
    right: 42px;
    top: 117px;
    text-align: right;
  }
  .identity__name {
    color: var(--brand-blue);
    font-weight: 700;
    font-size: 18px;
    line-height: 26px;
  }
  .identity__title {
    color: var(--ink-grey);
    font-size: 14px;
    line-height: 20px;
  }

  .contact-list {
    position: absolute;
    right: 42px;
    top: 172px;
    list-style: none;
    text-align: right;
  }
  .contact-list li {
    display: flex;
    justify-content: flex-end;
    align-items: center;
    gap: 7px;
    color: var(--ink-grey);
    font-size: 14.5px;
    line-height: 17.5px;
  }
  .contact-list svg { width: 10px; height: 10px; fill: var(--ink-grey); }

  .address {
    position: absolute;
    right: 42px;
    top: 249px;
    color: var(--ink-grey);
    font-size: 14.5px;
    line-height: 18px;
  }

  .card--back .wordmark {
    left: 0; right: 0;
    top: 104px;
    text-align: center;
    font-size: 50px;
  }
  .web-url {
    position: absolute;
    left: 0; right: 0;
    top: 176px;
    text-align: center;
    color: var(--ink-grey);
    font-size: 12px;
    letter-spacing: 3px;
  }
</style>
</head>
<body>
<main class="stage">
  <section class="card card--front" aria-label="Card front">
    <div class="wordmark">VARDEN</div>
    <div class="divider divider--left"></div>
    <div class="divider divider--right"></div>
    <div class="identity">
      <p class="identity__name">YOUR NAME</p>
      <p class="identity__title">Title</p>
    </div>
    <ul class="contact-list">
      <li>0987654321
        <svg viewBox="0 0 10 10" aria-label="Phone"><path d="M2 0.5 L3.8 2.6 L2.8 3.8 Q4 6.2 6.2 7.2 L7.4 6.2 L9.5 8 L8.3 9.5 Q3 9 0.5 1.7 Z"/></svg>
      </li>
      <li>0987654321
        <svg viewBox="0 0 10 10" aria-label="Fax"><path d="M2.5 0.5 H7.5 V3 H9.5 V9.5 H0.5 V3 H2.5 Z M3.5 1.5 V3 H6.5 V1.5 Z M2 5 V6 H8 V5 Z"/></svg>
      </li>
      <li>info@varden.com
        <svg viewBox="0 0 10 10" aria-label="Email"><path d="M0.5 2 H9.5 V8.5 H0.5 Z M1 2.4 L5 5.6 L9 2.4 Z" fill-rule="evenodd"/></svg>
      </li>
      <li>www.varden.com
        <svg viewBox="0 0 10 10" aria-label="Website"><circle cx="5" cy="5" r="4.3" fill="none" stroke="#4a4a4a" stroke-width="1"/><ellipse cx="5" cy="5" rx="1.8" ry="4.3" fill="none" stroke="#4a4a4a" stroke-width="0.8"/><path d="M0.7 5 H9.3" stroke="#4a4a4a" stroke-width="0.8"/></svg>
      </li>
    </ul>
    <p class="address">627 West Dorrance Blvd, Suite 308 Anaheim, CA 92718</p>
  </section>

  <section class="card card--back" aria-label="Card back">
    <div class="wordmark">VARDEN</div>
    <p class="web-url">www.varden.com</p>
  </section>
</main>
</body>
</html>
```